WordPress design (BRKT)

We need a wordpress design for an established auction and real estate company based in Viginia- "Bid Bold.... Move Swiftly!". The winning design will incorporate a professional color scheme with company logo in a clean layout.
Industry/Entity Type
Real Estate
Requirements
Must have
- Navigation:
- 1) Home
- 2) Services
- 3) Auctions
- 4) Gala Benefit
- 5) Appraisals
- 6) Past Successes
- 7) About BRKT
- 8) Contact us
- Colors will be those in the attached logo. design should be able to be developed in responsive theme. Wants a "very clean and professional and sharp" design. Site will have slideshow that is relatively small, not a large portion of the design. Please use stock real estate image.
- Footer will have attached logos and contact info for the client.
Nice to have
- A representative drop down menu will be nice to see.

```html
<!DOCTYPE html>
<html lang="en">
<head>
<meta charset="utf-8">
<title>BRKT – Auctions &amp; Real Estate</title>
<link href="https://fonts.googleapis.com/css2?family=Arimo:wght@400;700&family=Libre+Baskerville:wght@400;700&display=swap" rel="stylesheet">
<style>
:root{
  --gold:#c49d5b;
  --gold-dark:#9a7438;
  --ink:#2b2526;
  --panel:#3a3d40;
  --text:#333;
  --line:#d9d9d9;
  --paper:#fff;
  --soft:#fafafa;
}
*{box-sizing:border-box;margin:0;padding:0}
html,body{width:941px;height:1200px;overflow:hidden}
body{position:relative;background:var(--paper);font-family:"Arimo",Arial,sans-serif;color:var(--text);font-size:10.5px;line-height:1.4}
.abs{position:absolute}

/* header */
.site-header{left:0;top:36px;width:941px;height:64px;background:var(--ink);border-top:2px solid var(--gold)}
.brand{left:96px;top:10px;display:flex;align-items:center;gap:8px;font-family:"Libre Baskerville",Georgia,serif;font-size:24px;line-height:30px;color:#fff;letter-spacing:2px}
.brand-mark{width:16px;height:16px;background:var(--gold)}

/* nav */
.main-nav{left:0;top:100px;width:941px;height:31px;background:var(--gold);z-index:3}
.main-nav ul{list-style:none;display:flex;justify-content:space-between;margin-left:80px;width:781px;height:31px}
.main-nav li{position:relative;flex:1 1 auto;text-align:center}
.main-nav li+li::before{content:"";position:absolute;left:0;top:7px;height:18px;border-left:1px solid rgba(255,255,255,.55)}
.main-nav li.active::before,.main-nav li.active+li::before{display:none}
.main-nav li>a{display:block;color:#fff;text-decoration:none;font-weight:700;font-size:11px;height:31px;line-height:31px;white-space:nowrap}
.main-nav li.active>a{background:var(--panel);border-radius:5px 5px 0 0;margin:5px 4px 0;height:26px;line-height:24px}
.dropdown{position:absolute;left:4px;top:31px;width:130px;background:var(--panel);border-radius:0 4px 4px 4px;padding:2px 0;text-align:left}
.dropdown a{display:block;color:#fff;text-decoration:none;font-size:10px;line-height:14px;padding:4px 11px 4px;border-bottom:1px solid #4d5054}
.dropdown a:last-child{border:0}

/* hero */
.hero{left:80px;top:137px;width:562px;height:246px;background:linear-gradient(160deg,#b9c7d8 0%,#dfe3e6 35%,#8f8a7c 70%,#4b4a3b 100%)}
.featured{left:642px;top:137px;width:219px;height:246px;border:1px solid var(--line)}
.box-title{background:var(--gold);color:var(--ink);font-family:"Libre Baskerville",Georgia,serif;font-weight:700}
.featured .box-title{margin:2px;height:32px;line-height:32px;text-align:center;font-size:16.5px}
.featured h3{font-size:10.5px;font-weight:700;text-align:center;margin:12px 0 8px}
.featured .photo{margin:0 auto;width:176px;height:71px;background:linear-gradient(135deg,#5c6d3f,#2c2f2f 55%,#6b5a49)}
.featured p{font-size:9.6px;margin:14px 20px 0 22px;line-height:1.35}
.featured p+p{margin-top:4px}

/* welcome */
.welcome{left:81px;top:398px;width:545px}
.welcome h1{font-family:"Libre Baskerville",Georgia,serif;font-weight:400;font-size:19px;color:var(--ink);margin-bottom:8px}
.welcome h1 span{color:var(--gold);font-weight:700;letter-spacing:1px}
.welcome p{font-size:10.7px;line-height:1.38;padding-left:2px}
.welcome p+p{margin-top:14px}

/* listings */
.listing{left:82px;width:541px;height:246px;border:1px solid var(--line)}
.listing .box-title{position:absolute;left:4px;top:5px;width:531px;height:32px;line-height:32px;padding-left:8px;font-size:13.5px;letter-spacing:.3px}
.thumb-card{position:absolute;left:8px;top:53px;width:124px;height:134px;border:1px solid var(--line);border-radius:4px}
.thumb-card .photo{position:absolute;left:8px;top:8px;width:107px;height:73px;background:linear-gradient(170deg,#cfd8d4,#6f8c50 55%,#3f5a2a)}
.details-btn{position:absolute;left:8px;top:96px;width:107px;height:24px;background:var(--ink);color:#fff;font-size:13px;display:flex;align-items:center;gap:10px;padding-left:12px}
.info-card{position:absolute;left:137px;width:392px;border:1px solid var(--line);border-radius:4px;padding:5px 6px;background:var(--soft)}
.info-card.online{top:53px;height:87px}
.info-card.live{top:148px;height:87px}
.info-card h4{font-size:10.8px;font-weight:700;line-height:1.35;color:#222;letter-spacing:.25px}
.info-card p{font-size:10.3px;line-height:1.38;margin-top:3px;text-align:justify;letter-spacing:.25px;padding-right:14px}
.info-card .live-title{color:var(--gold-dark);font-size:10.8px;font-weight:700;letter-spacing:.2px}
.info-card.live p{margin-top:1px;text-align:left}

/* sidebar */
.signup{left:640px;top:398px;width:221px;height:118px;background:var(--gold);border:1px solid #a9844a;padding:7px 13px}
.signup h2{font-family:"Libre Baskerville",Georgia,serif;font-size:17px;color:var(--ink)}
.signup p{color:#fff;font-size:9.4px;margin-top:5px;line-height:1.35;padding-right:14px}
.signup form{display:flex;margin-top:12px;height:28px}
.signup .field{flex:1;background:#fff;border-radius:3px 0 0 3px;color:#aaa;font-size:9.5px;line-height:28px;padding-left:8px}
.signup .go{width:34px;background:var(--ink);color:#fff;font-weight:700;font-size:12px;text-align:center;line-height:28px;border-radius:0 3px 3px 0}

.video{left:640px;top:536px;width:221px;height:150px;border:1px solid var(--line)}
.video .frame{position:absolute;left:0;top:0;width:219px;height:134px;background:linear-gradient(175deg,#b7c3cd,#8e8574 55%,#5f7a45)}
.video .controls{position:absolute;left:0;top:134px;width:219px;height:14px;background:#111;color:#ccc;font-size:7px;display:flex;align-items:center;gap:6px;padding:0 6px}
.video .bar{width:75px;height:3px;background:#666;border-radius:2px}

.testimonials{left:640px;top:706px;width:221px;height:191px;border:1px solid var(--line)}
.testimonials .box-title{margin:2px;height:30px;line-height:30px;padding-left:14px;font-size:16.5px}
.testimonials blockquote{margin:12px 12px 0 14px;font-size:10.4px;line-height:1.5}
.testimonials .q{font-family:"Libre Baskerville",Georgia,serif;font-size:17px;font-weight:700;line-height:0;color:#222}
.testimonials cite{display:block;text-align:right;margin:5px 12px 0;color:var(--gold-dark);font-weight:700;font-size:10px}

.social{left:640px;top:913px;width:221px;height:100px;border:1px solid var(--line)}
.social .box-title{margin:2px;height:30px;line-height:30px;padding-left:10px;font-size:16.5px}
.social ul{list-style:none;display:flex;gap:11px;padding:11px 0 0 14px}
.social li{width:38px;height:38px;border-radius:3px;background:var(--panel)}
.social li:nth-child(2){background:var(--gold)}
.social li:nth-child(3){background:var(--gold-dark)}

/* footer */
.site-footer{left:0;top:1076px;width:941px;height:124px;background:var(--ink);border-top:5px solid var(--gold);color:#fff}
.site-footer address{position:absolute;left:93px;top:22px;font-style:normal;font-size:9.8px;line-height:1.45}
.site-footer .copy{position:absolute;left:93px;top:84px;font-size:9.8px}
.badge{position:absolute;background:#6a6566;border-radius:2px}
</style>
</head>
<body>

<header class="abs site-header">
  <div class="abs brand"><span class="brand-mark"></span>BRKT</div>
</header>

<nav class="abs main-nav">
  <ul>
    <li><a href="#">Home</a></li>
    <li><a href="#">Services</a></li>
    <li class="active"><a href="#">Auctions</a>
      <div class="dropdown">
        <a href="#">Staff Profile</a>
        <a href="#">Harlow News</a>
        <a href="#">Testimonials</a>
        <a href="#">Contact Us</a>
      </div>
    </li>
    <li><a href="#">Gala Benefit</a></li>
    <li><a href="#">Appraisals</a></li>
    <li><a href="#">Past Successes</a></li>
    <li><a href="#">About BRKT</a></li>
    <li><a href="#">Contact us</a></li>
  </ul>
</nav>

<div class="abs hero" role="img" aria-label="Suburban two-storey house at dusk with an auction sign on the lawn"></div>

<aside class="abs featured">
  <div class="box-title">Featured Listings</div>
  <h3>Multi Estate &amp; Consignment Auction</h3>
  <div class="photo" role="img" aria-label="Auctioneer calling bids to an outdoor crowd"></div>
  <p><b>Start Date/ Time:</b> Saturday, April 13, 2013 At 10:00 Am</p>
  <p><b>Location:</b> 418 Cedar Ridge,&nbsp; 73900</p>
</aside>

<section class="abs welcome">
  <h1>Welcome to <span>BRKT</span></h1>
  <p>simply dummy text of the printing and typesetting industry. Lorem Ipsum has been the industry's standard dummy text ever since the 1500s, when an unknown printer took a galley of type and scrambled it to make a type specimen book. remaining essentially unchanged. It was popularised in the 1960s with the release of</p>
  <p>Letraset sheets containing Lorem Ipsum passages, and more recently with scrambled it to make a type specimen book. remaining essentially unchanged.</p>
</section>

<article class="abs listing" style="top:536px">
  <h2 class="box-title">ONE STORY FRAME HOME ON 1.8 ACRES</h2>
  <div class="thumb-card">
    <div class="photo" role="img" aria-label="White one-story frame home among green trees"></div>
    <div class="details-btn"><svg width="14" height="14" viewBox="0 0 14 14"><circle cx="5.5" cy="5.5" r="4" fill="none" stroke="#fff" stroke-width="1.6"/><path d="M8.5 8.5l4 4" stroke="#fff" stroke-width="2"/></svg>Details</div>
  </div>
  <div class="info-card online">
    <h4>ONLINE NOW Internet Only Bidding Starts Closing Monday August 12th at 1:37PM</h4>
    <p>This former coffee cafe has closed and all items have been relocated to a sterling va warehouse for easy pick up.&nbsp; refrigerated equipment, counter top pizza ovens, chairs, stools, and more. ONLINE NOW!!! M1806</p>
  </div>
  <div class="info-card live">
    <div class="live-title">Live On-Site Auction</div>
    <p>Began:&nbsp; Friday, May 24, 2013 at 10:06 AM EDT</p>
    <p>Location<br>725 Maple Ct. NE<br>Fairview, IA 52000</p>
  </div>
</article>

<article class="abs listing" style="top:800px">
  <h2 class="box-title">ONE STORY FRAME HOME ON 1.8 ACRES</h2>
  <div class="thumb-card">
    <div class="photo" role="img" aria-label="White one-story frame home among green trees"></div>
    <div class="details-btn"><svg width="14" height="14" viewBox="0 0 14 14"><circle cx="5.5" cy="5.5" r="4" fill="none" stroke="#fff" stroke-width="1.6"/><path d="M8.5 8.5l4 4" stroke="#fff" stroke-width="2"/></svg>Details</div>
  </div>
  <div class="info-card online">
    <h4>ONLINE NOW Internet Only Bidding Starts Closing Monday August 12th at 1:37PM</h4>
    <p>This former coffee cafe has closed and all items have been relocated to a sterling va warehouse for easy pick up.&nbsp; refrigerated equipment, counter top pizza ovens, chairs, stools, and more. ONLINE NOW!!! M1806</p>
  </div>
  <div class="info-card live">
    <div class="live-title">Live On-Site Auction</div>
    <p>Began:&nbsp; Friday, May 24, 2013 at 10:06 AM EDT</p>
    <p>Location<br>725 Maple Ct. NE<br>Fairview, IA 52000</p>
  </div>
</article>

<aside class="abs signup">
  <h2>Email Sign-Up</h2>
  <p>Subscribe to Upcoming Auctions and our Free E-mail Newsletter.</p>
  <form><div class="field">Enter Your Email Address...</div><div class="go">Go</div></form>
</aside>

<aside class="abs video">
  <div class="frame" role="img" aria-label="Video still of a two-storey farmhouse with a front porch"></div>
  <svg class="abs" style="left:87px;top:45px" width="44" height="44" viewBox="0 0 44 44"><circle cx="22" cy="22" r="21" fill="#111"/><path d="M17 12l14 10-14 10z" fill="#fff"/></svg>
  <div class="controls">
    <svg width="7" height="7" viewBox="0 0 7 7"><path d="M0 0l7 3.5L0 7z" fill="#fff"/></svg>
    <span class="bar"></span><span>00:00 / 04:36</span>
  </div>
</aside>

<aside class="abs testimonials">
  <h2 class="box-title">Clients Testimonials</h2>
  <blockquote><span class="q">&ldquo;</span> Contrary to popular belief, Lorem Ipsum is not simply random text. It has roots in a piece of classical Latin literature from 45 BC, making it over 2000 years old. Richard random text. It has roots in a piece of Harrowgate, It has roots in a making. <span class="q">&rdquo;</span></blockquote>
  <cite>By Daniel Weston</cite>
</aside>

<aside class="abs social">
  <h2 class="box-title">Social Media</h2>
  <ul><li></li><li></li><li></li><li></li></ul>
</aside>

<footer class="abs site-footer">
  <address>840 W. Central &bull; Redhill, OK 73000<br>Office: (555) 201-4410<br>Toll-Free: (800) 555-0142<br>Email: brktauctions@example.com</address>
  <div class="copy">Copyright &copy; 2013 BRKT . All rights reserved.</div>
  <span class="badge" style="left:384px;top:22px;width:28px;height:30px"></span>
  <span class="badge" style="left:424px;top:25px;width:58px;height:22px"></span>
  <span class="badge" style="left:494px;top:22px;width:32px;height:28px"></span>
  <span class="badge" style="left:538px;top:25px;width:57px;height:22px"></span>
  <span class="badge" style="left:614px;top:24px;width:42px;height:24px"></span>
  <span class="badge" style="left:680px;top:20px;width:40px;height:32px"></span>
  <span class="badge" style="left:737px;top:16px;width:36px;height:36px"></span>
  <span class="badge" style="left:792px;top:20px;width:55px;height:30px"></span>
  <span class="badge" style="left:578px;top:64px;width:58px;height:22px"></span>
  <span class="badge" style="left:652px;top:60px;width:34px;height:32px"></span>
  <span class="badge" style="left:702px;top:58px;width:58px;height:32px"></span>
  <span class="badge" style="left:784px;top:59px;width:63px;height:32px"></span>
</footer>

</body>
</html>
```